Verpackungsdesign für Pasta aus Buchweizen
Zielgruppe
Unser Unternehmen VELMORIA sucht ein sehr modernes Verpackungsdesign für Pasta aus Buchweizen.
Unsere Produkte sind in unserem Online Shop und unterscheiden sich durch die herkömmliche Pasta, da wir Buchweizen in die Verarbeitung mit aufnehmen und somit die gesundheitsfördernde Eigenschaft des Buchweizens im Vordergrund steht. Unsere Pasta aus Buchweizenmehl mit klassischem Hartweizengrieß ist in dieser Form noch nicht im stationären Handel erhältlich, deshalb wünschen wir uns ein neues, ansprechendes Verpackungsdesign welches von den Massenprodukten aus den Regalen im Handel heraussticht. Das Design sollte also minimalistisch und sehr modern wirken, und sich deutlich von der Konkurrenz abheben.
Die Zielgruppe richtet sich sowohl an Massen die Pasta in allen Variationen lieben, als auch an ernährungsbewusste Veganer/Vegetarier die Alternativen im Bereich der herkömmlichen Pasta Kochkultur suchen.
PS: Mit dem Verkauf unserer Pasta investieren wir außerdem in den Aufbau und der Infrastruktur des Erzeugerlandes. Durch unser Prinzip „Teilen & Wachsen“ fördern wir mit unseren Gewinnen nachhaltige Projekte in den Erzeugerländern und helfen somit wirtschaftlich benachteiligten Regionen auf der Welt. (Fair Trade)
Aufgabenstellung
Wir besitzen bereits ein Logo und Verpackungen für unsere Pasta Sorten. Das Logo und das Grundgerüst der Stanzform / Verpackungsmaße (inkl. Sichtfenster) soll beibehalten werden (Siehe Anhang). Als Pasta Verpackungen benutzen wir Faltschachteln und Banderolen.
Verpackungsmaße:
- Faltschachtel (90 x 40 x 165 mm)
- Banderole (560 x 70mm)
Der Produktname ist je nach Sorte zu präzisieren:
- Fusilli
- Makkaroni
- Bandnudeln
- Tarhana
Produktgewicht:
- 250g
Eigenschaften:
- Buchweizenmehl
- 100% Vegan
- Kochzeit 3 Minuten
- Liebevolle Handarbeit
WICHTIG:
1) Bitte benutzt die hochgeladene, leere Stanzform für Artwork.
2) Die Designfarbe kann anhand des Aufstellers ausgerichtet werden (CMYK: 0, 20, 32, 0 und 60, 57, 56, 62) es ist aber kein muss und ihr seit frei in der Kreativität.
3) Bitte das Sichtfenster mit Rand wie aktuell auf den Produkten übernehmen (siehe www.velmoria.de/shop)
Nach dem Wettbewerb planen wir zusätzlich ein 1zu1 Projekt und würden uns freuen einen Gewinner auszuwählen - Wir freuen uns auf eure Ideen :)

```html
<!DOCTYPE html>
<html lang="de">
<head>
<meta charset="utf-8">
<title>VELMORIA Buchweizen Pasta – Faltschachtel</title>
<link href="https://fonts.googleapis.com/css2?family=Bebas+Neue&family=Josefin+Sans:wght@300;400&family=Open+Sans:wght@400&family=Playfair+Display:ital@1&display=swap" rel="stylesheet">
<style>
  :root {
    --stage: #d9d9d9;
    --carton: #ffffff;
    --ink: #111111;
    --brown: #9b7168;
    --brown-dark: #5a3c33;
    --pasta-light: #b88a5e;
    --pasta-dark: #6b4326;
    --seed-tint: #ece8e6;
    --vegan: #5f9a3c;
    --text-grey: #444444;
  }
  * { margin: 0; padding: 0; box-sizing: border-box; }
  html, body { width: 1200px; height: 1148px; overflow: hidden; }
  body { background: var(--stage); position: relative; font-family: 'Josefin Sans', sans-serif; }

  .carton { position: absolute; left: 245px; top: 124px; width: 709px; height: 900px; display: flex; box-shadow: 0 18px 40px rgba(0,0,0,0.12); }
  .panel { position: relative; height: 100%; background: var(--carton); }
  .panel--side { width: 218px; border-right: 1px solid #e6e6e6; }
  .panel--front { width: 491px; }

  /* side panel */
  .cook-time { position: absolute; top: 196px; left: 0; width: 100%; text-align: center; font-weight: 300; font-size: 19px; line-height: 25px; color: var(--text-grey); letter-spacing: 0.5px; }
  .cook-time strong { font-weight: 400; }
  .pot-icon { position: absolute; top: 262px; left: 58px; width: 96px; height: 96px; }
  .info-text { position: absolute; left: 24px; width: 170px; font-family: 'Open Sans', sans-serif; font-size: 8px; line-height: 10px; color: var(--text-grey); text-align: justify; }
  .info-text--intro { top: 408px; }
  .info-text--details { top: 496px; }
  .info-text--prep { top: 562px; }
  .vegan-badge { position: absolute; left: 66px; top: 770px; width: 50px; height: 50px; border-radius: 50%; background: var(--vegan); border: 3px solid #fff; box-shadow: 0 0 0 2px var(--vegan); }
  .net-weight { position: absolute; left: 0; top: 846px; width: 100%; text-align: center; font-size: 17px; font-weight: 300; color: var(--text-grey); }

  /* variety band crossing both panels */
  .variety-band { position: absolute; left: 0; top: 448px; width: 465px; height: 46px; background: var(--brown); }
  .variety-name { position: absolute; left: 268px; top: 453px; font-family: 'Playfair Display', serif; font-style: italic; font-size: 28px; color: #fff; }

  /* front panel */
  .brand { position: absolute; top: 70px; left: 0; width: 100%; text-align: center; font-family: 'Bebas Neue', sans-serif; font-size: 40px; letter-spacing: 3px; color: var(--brown-dark); }
  .brand-dot { display: inline-block; width: 10px; height: 10px; border-radius: 50%; background: var(--brown-dark); margin-left: 8px; vertical-align: 8px; }
  .product-title { position: absolute; top: 222px; left: 60px; font-family: 'Bebas Neue', sans-serif; font-weight: 400; font-size: 84px; line-height: 70px; color: var(--ink); letter-spacing: 0.5px; }
  .script-label { position: absolute; top: 312px; left: 225px; width: 190px; height: 52px; background: var(--seed-tint); border-radius: 4px; }
  .window { position: absolute; left: 60px; top: 540px; width: 400px; height: 330px; }
  .seed-sketches { position: absolute; left: 330px; top: 530px; width: 110px; height: 330px; background: var(--seed-tint); border-radius: 50px; opacity: 0.7; }
</style>
</head>
<body>
  <div class="carton">
    <section class="panel panel--side">
      <p class="cook-time">KOCHZEIT<br><strong>3 MINUTEN</strong></p>
      <svg class="pot-icon" viewBox="0 0 96 96" fill="none" stroke="#111" stroke-width="2.2" stroke-linecap="round" stroke-linejoin="round" aria-hidden="true">
        <path d="M20 34 h50 v30 a8 8 0 0 1 -8 8 h-34 a8 8 0 0 1 -8 -8 z"/>
        <path d="M14 40 h6 M70 40 h6"/>
        <path d="M24 30 q21 -10 42 0"/>
        <path d="M41 22 h8"/>
        <path d="M24 58 q5 -5 10 0 t10 0 t10 0 t10 0"/>
        <path d="M68 22 q6 -6 2 -12 M76 26 q6 -8 2 -14"/>
        <path d="M32 84 q-3 4 0 6 q3 -2 0 -6 M45 84 q-3 4 0 6 q3 -2 0 -6 M58 84 q-3 4 0 6 q3 -2 0 -6"/>
      </svg>
      <p class="info-text info-text--intro">Feine Pasta aus Buchweizenmehl und Hartweizengrieß, mit liebevoller Handarbeit hergestellt.</p>
      <p class="info-text info-text--details">Zutaten: Buchweizenmehl, Hartweizengrieß, Wasser. Kann Spuren von Soja enthalten. Trocken und kühl lagern. Nach dem Öffnen gut verschließen.</p>
      <p class="info-text info-text--prep">Zubereitung: Pasta in reichlich kochendes Salzwasser geben und drei Minuten garen. Abgießen und sofort servieren. Mit jedem Kauf unterstützt du nachhaltige Projekte in den Erzeugerländern – nach unserem Prinzip „Teilen &amp; Wachsen“.</p>
      <div class="vegan-badge" aria-hidden="true"></div>
      <p class="net-weight">250g ℮</p>
    </section>

    <section class="panel panel--front">
      <p class="brand">VELMORIA<span class="brand-dot"></span></p>
      <h1 class="product-title">BUCHWEIZEN<br>PASTA</h1>
      <div class="script-label" role="img" aria-label="Handgeschriebener Schriftzug „Buckwheat“"></div>
      <div class="seed-sketches" role="img" aria-label="Skizzierte Buchweizenkörner"></div>
      <svg class="window" viewBox="0 0 400 330" role="img" aria-label="Sichtfenster in Blattform mit Blick auf die Buchweizen-Fusilli">
        <defs>
          <linearGradient id="pasta" x1="0" y1="0" x2="1" y2="1">
            <stop offset="0" stop-color="var(--pasta-light)"/>
            <stop offset="1" stop-color="var(--pasta-dark)"/>
          </linearGradient>
        </defs>
        <path d="M160 180 C140 110 190 40 250 10 C275 80 250 160 185 200 Z" fill="url(#pasta)"/>
        <path d="M12 168 C70 140 150 170 180 230 C140 260 60 270 20 300 C8 260 6 210 12 168 Z" fill="url(#pasta)"/>
        <path d="M190 330 C180 260 220 200 290 175 C300 240 260 300 190 330 Z" fill="url(#pasta)"/>
      </svg>
      <span class="variety-band-front" aria-hidden="true"></span>
    </section>

    <div class="variety-band" aria-hidden="true"></div>
    <p class="variety-name">fusilli</p>
  </div>
</body>
</html>
```